Copper Field Agency Website - Wordpress Web UPDATED BRIEF

FINAL LOGO UPLOADED - please look to this as reference for how we would like the site to look and feel.

We are a digital marketing agency - looking to have a new website built. We are looking for a simple one page feel of site that will allow us to grow it later. (Feel free to take some liberties with that if your imagination veers off) Must be very, playful, bold, sleek and easily integrate video. Wordpress only.

Overview:

Copper Field is a creative constellation. We are built on what's great about the shared economy. With access to thousands of content creators, designers, technicians, writers, strategists and other creatives around the world, we are built differently than a traditional “brick and mortar” Marketing Agency. We provide the traditional services our clients have come to expect, without the “5X factor” of covering the overhead common in the old agency model. We believe even better work can be created in collaboration with our clients and by passing those savings back to them for their use. Our clients pay for our art, our work and our passion –not our furniture.

"Copper Field, Let's Build Together"

Target Market(s)

companies looking for creative agency help, video production, creative consulting and coaching

Industry/Entity Type

Digital Marketing

Coding

Coded - Design and coding required

Number of Pages Required

1 page

Font styles to use
Sans Serif

Colors
3277b5
33a6d7
ec1f27

Requirements
Must have
• Wordpress design is a must. Looking for a one sheet homepage - with sections that are all on the main front page. We will have videos to embed, and should be able to have client logos and easy access to show a variety of our creative work.
• Please look to the logo for how we would like the site to feel.
• Please think "icon process flow" instead of blocks of text (which we used to have). Use the text to explain what the process flow should represent - don't actually copy paste the text but show it visually in icons.
Nice to have
• innovation around how we show video content. solid colors complementary to our palette and aesthetic.
Should not have
• Standard HTML coding

```html
<!DOCTYPE html>
<html lang="en">
<head>
<meta charset="utf-8">
<title>Copper Field Agency</title>
<link href="https://fonts.googleapis.com/css2?family=Open+Sans:ital,wght@0,400;0,600;0,700;0,800;1,400;1,700&display=swap" rel="stylesheet">
<style>
:root{
  --blue:#3277b5;
  --sky:#33a6d7;
  --red:#ec1f27;
  --ink:#333;
  --muted:#666;
  --dark:#1c1d20;
  --white:#fff;
  --mist:#eef1f4;
}
*{box-sizing:border-box;margin:0;padding:0}
html,body{width:1200px;height:4220px;overflow:hidden}
body{font-family:"Open Sans",Arial,sans-serif;color:var(--ink);background:var(--white);position:relative}
.abs{position:absolute}
.btn{display:inline-block;background:var(--red);color:var(--white);font-weight:700;font-size:15px;text-transform:uppercase;text-align:center;letter-spacing:.3px}

/* hero */
.hero{position:absolute;left:0;top:0;width:1200px;height:600px;overflow:hidden}
.hero-photo{position:absolute;inset:0;background:linear-gradient(110deg,#3c4650 0%,#6d7680 35%,#9aa1a8 60%,#5e6670 100%)}
.hero-shade{position:absolute;inset:0;background:linear-gradient(90deg,rgba(20,28,40,.55),rgba(20,28,40,.15))}
.brand{position:absolute;left:88px;top:14px;display:flex;align-items:center;gap:10px;color:var(--white);font-weight:800;font-size:20px}
.brand-dot{width:46px;height:46px;border-radius:50%;background:var(--sky)}
.topbar{position:absolute;right:88px;top:16px;display:flex;gap:36px;color:var(--white);font-size:14px}
.topbar span{display:flex;align-items:center;gap:8px}
.nav{position:absolute;right:88px;top:60px;display:flex;gap:22px;color:var(--white);font-size:15px;font-weight:600}
.hero-title{position:absolute;left:88px;top:200px;color:var(--white);font-size:46px;font-weight:700}
.hero-text{position:absolute;left:88px;top:282px;width:500px;color:var(--white);font-size:18px;line-height:27px}
.hero .btn{position:absolute;left:88px;top:398px;width:248px;height:54px;line-height:54px;font-size:16px}
.hero-wave{position:absolute;left:0;bottom:0}

/* about */
.section-title{color:var(--blue);font-weight:700;font-size:42px}
.about-title{left:88px;top:724px}
.about-text{left:88px;top:820px;width:450px;font-size:15px;line-height:27px;color:var(--muted)}
.about .btn{left:88px;top:1044px;width:162px;height:50px;line-height:50px}
.about-photo{left:628px;top:688px;width:472px;height:472px;background:linear-gradient(135deg,#d7e3ee,#7ea6c9 55%,#c9d4de)}

/* services */
.services{left:0;top:1268px;width:1200px;height:540px;background:linear-gradient(120deg,#e8ebee,#f5f6f7 50%,#dfe3e7)}
.services-title{left:0;top:50px;width:1200px;text-align:center;font-size:40px}
.flow{position:absolute;left:0;top:0}

/* trusted */
.trusted-title{left:0;top:1926px;width:1200px;text-align:center;color:var(--blue);font-weight:700;font-size:31px}
.clients{left:88px;top:2040px;width:1024px;display:flex;justify-content:space-between;align-items:center}
.client{display:flex;align-items:center;gap:10px;font-weight:700;font-size:18px;color:var(--blue)}
.client i{display:block;width:36px;height:36px;border-radius:50%;background:var(--sky)}

/* testimonials */
.testimonials{left:0;top:2204px;width:1200px;height:436px;background:linear-gradient(100deg,#2e6ea9,var(--blue) 45%,#3b8cc6)}
.quote-badge{left:588px;top:56px;width:26px;height:26px;border-radius:50%;background:var(--red);color:var(--white);font-weight:800;font-size:20px;text-align:center;line-height:30px}
.quote-text{left:200px;top:246px;width:800px;text-align:center;color:var(--white);font-style:italic;font-size:17px;line-height:28px}
.quote-name{left:0;top:340px;width:1200px;text-align:center;color:var(--white);font-style:italic;font-weight:700;font-size:20px}

/* gallery */
.gallery-title{left:0;top:2800px;width:1200px;text-align:center}
.gallery-text{left:200px;top:2902px;width:800px;text-align:center;font-size:18px;line-height:30px;color:var(--ink)}
.tile{position:absolute;width:324px;height:220px}
.gallery .btn{left:468px;top:3546px;width:264px;height:58px;line-height:58px}

/* footer */
.footer{left:0;top:3640px;width:1200px;height:580px}
.footer-body{position:absolute;left:0;top:80px;width:1200px;height:500px;background:var(--dark)}
.footer .brand{left:88px;top:118px;position:absolute}
.footer-about{left:88px;top:206px;width:280px;color:#ccc;font-size:14px;line-height:24px}
.fcol{top:130px;color:#ccc;font-size:14px;line-height:25px}
.fcol h4{color:var(--white);font-size:20px;font-weight:700;margin-bottom:14px}
.fcol.contact p{display:flex;gap:10px;margin-bottom:6px}
.footer-rule{left:88px;top:508px;width:1024px;height:1px;background:#3a3b3f}
.copyright{left:88px;top:526px;color:#aaa;font-size:13px}
.socials{right:88px;top:524px;display:flex;gap:10px}
.socials i{display:block;width:20px;height:20px;background:#8b8d92;border-radius:3px}
</style>
</head>
<body>

<header class="hero">
  <div class="hero-photo" role="img" aria-label="Team of creatives gathered around a table in a bright office"></div>
  <div class="hero-shade"></div>
  <div class="brand"><span class="brand-dot"></span>Copper Field</div>
  <div class="topbar">
    <span><svg width="16" height="12" viewBox="0 0 16 12"><rect x="0.5" y="0.5" width="15" height="11" fill="none" stroke="#fff"/><path d="M1 1l7 6 7-6" fill="none" stroke="#fff"/></svg>hello@copperfield-agency.com</span>
    <span><svg width="14" height="14" viewBox="0 0 24 24"><path fill="#fff" d="M6.6 10.8a15 15 0 006.6 6.6l2.2-2.2c.3-.3.7-.4 1-.2 1.1.4 2.3.6 3.6.6.6 0 1 .4 1 1V20c0 .6-.4 1-1 1A17 17 0 013 4c0-.6.4-1 1-1h3.5c.6 0 1 .4 1 1 0 1.3.2 2.5.6 3.6.1.3 0 .7-.2 1z"/></svg>555-014-2290</span>
  </div>
  <nav class="nav"><span>Home</span><span>About Us</span><span>Services</span><span>Our Clients</span><span>Testimonials</span><span>Gallery</span><span>Contact Us</span></nav>
  <h1 class="hero-title">Copper Field</h1>
  <p class="hero-text">We are built on what's great about the shared economy. With access to thousands of content creators, designers, technicians.</p>
  <span class="btn">Request a Quote</span>
  <svg class="hero-wave" width="1200" height="180" viewBox="0 0 1200 180"><path fill="#fff" d="M0 120 C180 40 330 60 500 120 S850 200 1020 110 C1100 70 1160 60 1200 70 L1200 180 L0 180Z"/></svg>
</header>

<section class="about">
  <h2 class="section-title abs about-title">About Us</h2>
  <p class="abs about-text">Copper Field is a creative constellation. We are built on what's great about the shared economy. With access to thousands of content creators, designers, technicians, writers, strategists and other creatives around the world, we are built differently than a traditional “brick and mortar” Marketing Agency.</p>
  <span class="btn abs">Read More</span>
  <div class="abs about-photo" role="img" aria-label="Hands working on a laptop with digital network icons overlay"></div>
</section>

<section class="abs services" aria-label="Services">
  <h2 class="section-title abs services-title">Services</h2>
  <svg class="flow" width="1200" height="540" viewBox="0 0 1200 540" font-family="Open Sans, Arial, sans-serif">
    <defs>
      <linearGradient id="dia" x1="0" y1="0" x2="1" y2="1"><stop offset="0" stop-color="#33a6d7"/><stop offset="1" stop-color="#3277b5"/></linearGradient>
      <marker id="arrow" markerWidth="8" markerHeight="8" refX="6" refY="4" orient="auto"><path d="M0 0L8 4L0 8Z" fill="#222"/></marker>
    </defs>
    <g stroke="#222" stroke-width="2.5" fill="none" marker-end="url(#arrow)">
      <path d="M250 258 L282 318"/><path d="M370 318 L412 240"/><path d="M510 238 L544 318"/>
      <path d="M636 318 L676 240"/><path d="M772 238 L806 318"/><path d="M900 318 L934 240"/>
    </g>
    <g fill="url(#dia)" stroke="#fff" stroke-width="4">
      <rect x="160" y="140" width="90" height="90" transform="rotate(45 205 185)"/>
      <rect x="275" y="270" width="90" height="90" transform="rotate(45 320 315)"/>
      <rect x="415" y="140" width="90" height="90" transform="rotate(45 460 185)"/>
      <rect x="543" y="270" width="90" height="90" transform="rotate(45 588 315)"/>
      <rect x="675" y="140" width="90" height="90" transform="rotate(45 720 185)"/>
      <rect x="807" y="270" width="90" height="90" transform="rotate(45 852 315)"/>
      <rect x="935" y="140" width="90" height="90" transform="rotate(45 980 185)"/>
    </g>
    <g fill="none" stroke="#fff" stroke-width="2.5">
      <circle cx="203" cy="168" r="10"/><path d="M210 175l8 8"/>
      <circle cx="320" cy="298" r="11"/><circle cx="320" cy="298" r="4"/>
      <rect x="448" y="160" width="24" height="18"/><path d="M454 166h12M454 172h8"/>
      <rect x="576" y="288" width="24" height="18"/><path d="M586 292l8 5-8 5z"/>
      <circle cx="720" cy="169" r="9"/><path d="M720 154v5M720 179v5M705 169h5M730 169h5"/>
      <path d="M840 306l8-10 6 6 10-12"/>
      <path d="M968 178l6-12 6 8 6-8 6 12"/>
    </g>
    <g fill="#fff" font-size="12" font-weight="700" text-anchor="middle">
      <text x="205" y="210">Discovery</text>
      <text x="320" y="338">Strategy</text>
      <text x="460" y="202">Project</text><text x="460" y="216">Management</text>
      <text x="588" y="338">Content</text>
      <text x="720" y="210">Production</text>
      <text x="852" y="330">Paid</text><text x="852" y="344">Media</text>
      <text x="980" y="210">Coaching</text>
    </g>
  </svg>
</section>

<section class="trusted">
  <h2 class="abs trusted-title">Trusted By 17,000+ Happy Customers Worldwide</h2>
  <div class="abs clients">
    <span class="client"><i></i>Loomwork Labs</span>
    <span class="client"><i></i>Kestrel</span>
    <span class="client"><i></i>Brightline Software</span>
    <span class="client"><i></i>Northbay Institute</span>
    <span class="client"><i></i>Solace Group</span>
  </div>
</section>

<section class="abs testimonials" aria-label="Testimonials">
  <span class="abs quote-badge">“</span>
  <svg class="abs" style="left:0;top:0" width="1200" height="240" viewBox="0 0 1200 240">
    <g fill="#d9dde2" stroke="#fff" stroke-width="4">
      <polygon points="252,162 279,178 279,210 252,226 225,210 225,178" transform="translate(0,-6)"/>
      <polygon points="400,160 428,176 428,210 400,226 372,210 372,176" transform="translate(0,-6)"/>
      <polygon points="600,116 652,146 652,206 600,236 548,206 548,146"/>
      <polygon points="792,160 820,176 820,210 792,226 764,210 764,176" transform="translate(0,-6)"/>
      <polygon points="948,162 975,178 975,210 948,226 921,210 921,178" transform="translate(0,-6)"/>
    </g>
    <g fill="#fff"><circle cx="40" cy="200" r="14"/><circle cx="1160" cy="200" r="14"/></g>
    <g fill="#3277b5"><path d="M44 193l-8 7 8 7z"/><path d="M1156 193l8 7-8 7z"/></g>
  </svg>
  <p class="abs quote-text">“Copper Field is proving to be a force in the creative consulting industry and we look forward to collaborating with them again in the future.”</p>
  <p class="abs quote-name">Marla Quinn, Harbor Stage</p>
</section>

<section class="gallery">
  <h2 class="section-title abs gallery-title">Gallery</h2>
  <p class="abs gallery-text">Lorem ipsum dolor sit amet, consectetur adipiscing elit. Quisque condimentum sed elit eget vulputate. Donec maximus nec libero vitae</p>
  <div class="tile" style="left:88px;top:3020px;background:linear-gradient(135deg,#1e3c66,#3a78b2)" role="img" aria-label="Digital workspace with glowing data screens"></div>
  <div class="tile" style="left:438px;top:3020px;background:linear-gradient(135deg,#8a5a3c,#c99a74 50%,#3d4a5a)" role="img" aria-label="Colleagues presenting ideas beside a screen"></div>
  <div class="tile" style="left:788px;top:3020px;background:linear-gradient(135deg,#b59a7c,#e3d4bf)" role="img" aria-label="Team hands meeting over a shared desk"></div>
  <div class="tile" style="left:88px;top:3262px;background:linear-gradient(135deg,#cfd8e0,#8fa5b8)" role="img" aria-label="Hands using a tablet with charts"></div>
  <div class="tile" style="left:438px;top:3262px;background:linear-gradient(135deg,#0d2a52,#2f6fb0 60%,#9cc4e6)" role="img" aria-label="Hand touching a glowing network interface"></div>
  <div class="tile" style="left:788px;top:3262px;background:linear-gradient(135deg,#c7c9cc,#f0efec)" role="img" aria-label="Small team reviewing work at a laptop"></div>
  <span class="btn abs">View More Gallery</span>
</section>

<footer class="abs footer">
  <svg class="abs" style="left:0;top:0" width="1200" height="100" viewBox="0 0 1200 100"><path fill="#1c1d20" d="M0 60 C180 0 360 10 540 60 S900 110 1200 30 L1200 100 L0 100Z"/></svg>
  <div class="footer-body"></div>
  <div class="brand"><span class="brand-dot"></span>Copper Field</div>
  <p class="abs footer-about">We provide the traditional services our clients have come to expect, without the “5X factor” of covering the overhead common in the old agency model.</p>
  <div class="abs fcol" style="left:452px"><h4>Quick Links</h4><p>Home</p><p>About Us</p><p>Services</p><p>Our Clients</p><p>Testimonials</p><p>Gallery</p><p>Contact Us</p></div>
  <div class="abs fcol" style="left:640px"><h4>Services</h4><p>Discovery</p><p>Strategy</p><p>Project Management</p><p>Content</p><p>Production</p><p>Paid Media</p><p>Coaching</p></div>
  <div class="abs fcol contact" style="left:884px"><h4>Contact Us</h4>
    <p><svg width="12" height="16" viewBox="0 0 12 16"><path fill="#fff" d="M6 0a6 6 0 00-6 6c0 4.5 6 10 6 10s6-5.5 6-10a6 6 0 00-6-6zm0 8.5A2.5 2.5 0 116 3.5a2.5 2.5 0 010 5z"/></svg><span>42 Alder Lane West,<br>Harbourview, VIC</span></p>
    <p><svg width="13" height="13" viewBox="0 0 24 24"><path fill="#fff" d="M6.6 10.8a15 15 0 006.6 6.6l2.2-2.2c.3-.3.7-.4 1-.2 1.1.4 2.3.6 3.6.6.6 0 1 .4 1 1V20c0 .6-.4 1-1 1A17 17 0 013 4c0-.6.4-1 1-1h3.5c.6 0 1 .4 1 1 0 1.3.2 2.5.6 3.6.1.3 0 .7-.2 1z"/></svg>555-014-2290</p>
    <p><svg width="14" height="11" viewBox="0 0 16 12"><rect x="0.5" y="0.5" width="15" height="11" fill="none" stroke="#fff"/><path d="M1 1l7 6 7-6" fill="none" stroke="#fff"/></svg>hello@copperfield-agency.com</p>
  </div>
  <div class="abs footer-rule"></div>
  <p class="abs copyright">© Copper Field Agency 2019. All rights reserved.</p>
  <div class="abs socials"><i></i><i></i><i></i><i></i><i></i><i></i></div>
</footer>

</body>
</html>
```